Law Firm Profile

I need a Law firm Profile design. Something professional, corporate inspired, unique and sophisticated. Preferred colours are blue, grey and white. Completion timeline is 5 days. Details of law firm are in the uploaded document

```html
<!DOCTYPE html>
<html lang="en">
<head>
<meta charset="utf-8">
<title>KNB Advocates – Law Firm Profile</title>
<link href="https://fonts.googleapis.com/css2?family=Montserrat:wght@400;500;600;700;800&display=swap" rel="stylesheet">
<style>
  :root {
    --navy: #0c3f7c;
    --blue: #1565b5;
    --sky: #1fa3e6;
    --grey: #5f6166;
    --mist: #eceef1;
    --paper: #f7f8f9;
    --ink: #2b2d31;
    --white: #ffffff;
  }
  * { box-sizing: border-box; margin: 0; padding: 0; }
  html, body { width: 720px; height: 1200px; overflow: hidden; }
  body {
    background: #e4e5e8;
    font-family: "Montserrat", Arial, sans-serif;
    color: var(--ink);
    position: relative;
  }
  .page {
    position: absolute;
    width: 350px;
    height: 495px;
    overflow: hidden;
    background: linear-gradient(160deg, var(--paper), #e3e5e9);
    box-shadow: 0 2px 8px rgba(0,0,0,.12);
  }
  .page svg.shapes { position: absolute; inset: 0; }
  .abs { position: absolute; }

  /* covers */
  .brand {
    position: absolute; left: 62px; top: 40px;
    font-weight: 800; font-size: 27px; letter-spacing: .5px;
    color: var(--navy); line-height: 1;
  }
  .tagline {
    position: absolute; left: 88px; top: 80px;
    font-weight: 500; font-size: 14px; letter-spacing: 4px;
    color: var(--grey);
  }

  /* back cover contact */
  .contact {
    position: absolute; left: 110px; top: 150px; width: 230px;
    color: var(--white); font-weight: 700; font-size: 9.5px;
    line-height: 1.35; text-align: center;
  }
  .contact h3 { color: var(--sky); font-size: 10px; letter-spacing: 1px; margin-bottom: 8px; }
  .contact p { margin-bottom: 8px; }

  /* inner pages */
  .intro {
    position: absolute; left: 108px; top: 44px; width: 228px;
    font-weight: 700; font-size: 8.2px; line-height: 1.35;
  }
  .col { position: absolute; font-size: 5.3px; line-height: 1.35; }
  .col p { margin-bottom: 5px; }
  .col b { color: var(--blue); font-weight: 700; text-transform: uppercase; }

  .section-title { font-weight: 800; letter-spacing: 1px; text-transform: uppercase; }
  .personnel-title { left: 36px; top: 176px; color: var(--white); font-size: 13px; transform: rotate(-8deg); transform-origin: left; }
  .person-name { font-weight: 800; font-size: 7px; color: var(--blue); line-height: 1.15; }
  .person-role { font-size: 5px; color: var(--grey); letter-spacing: .5px; text-transform: uppercase; }
  .bio { font-size: 5.2px; line-height: 1.38; }
  .mgmt-title { left: 20px; top: 332px; color: var(--blue); font-size: 12px; }
  .mgmt-intro { left: 20px; top: 352px; width: 315px; font-size: 5.4px; line-height: 1.4; }
  .mgmt-list { left: 22px; top: 384px; list-style: none; font-size: 6.2px; font-weight: 700; color: var(--blue); line-height: 1.75; }
  .mgmt-list span { color: var(--ink); margin-right: 4px; }
  .values { left: 168px; top: 416px; width: 170px; color: var(--white); }
  .values h4 { font-size: 9px; font-weight: 800; text-align: right; margin-bottom: 4px; letter-spacing: .5px; }
  .values p { font-size: 5.1px; line-height: 1.4; text-align: right; }
</style>
</head>
<body>

<!-- Back cover -->
<section class="page back-cover" style="left:10px; top:50px;">
  <svg class="shapes" width="350" height="495" viewBox="0 0 350 495">
    <defs>
      <linearGradient id="meetingTone" x1="0" y1="0" x2="1" y2="1">
        <stop offset="0" stop-color="#cfc6b9"/><stop offset="1" stop-color="#8e8880"/>
      </linearGradient>
      <linearGradient id="officeTone" x1="0" y1="0" x2="1" y2="1">
        <stop offset="0" stop-color="#7c7e84"/><stop offset="1" stop-color="#44464b"/>
      </linearGradient>
      <linearGradient id="bandBlue" x1="0" y1="0" x2="1" y2="1">
        <stop offset="0" stop-color="#1565b5"/><stop offset="1" stop-color="#0c3f7c"/>
      </linearGradient>
    </defs>
    <rect role="img" aria-label="Photo of lawyers in a meeting at a desk" x="0" y="0" width="350" height="270" fill="url(#meetingTone)"/>
    <rect role="img" aria-label="Photo of a client consultation in an office" x="0" y="270" width="350" height="225" fill="url(#officeTone)"/>
    <path d="M40 230 C150 215 260 170 350 110 L350 340 C250 370 170 420 110 470 Z" fill="url(#bandBlue)"/>
  </svg>
  <div class="contact">
    <h3>CONTACT INFORMATION</h3>
    <p>Plot No. 14, Kafue Crescent,<br>Rhodes Vale</p>
    <p>P.O. Box 40210, Woodlands,<br>Lusaka, Zambia</p>
    <p>Cell: +260 770 100 201,<br>+260 950 100 302, +260 760 100 504<br>+260 970 100 403</p>
    <p>Tel: +260 211 000 145</p>
    <p>Email: info@knbadvocates.example</p>
  </div>
</section>

<!-- Front cover -->
<section class="page front-cover" style="left:360px; top:50px;">
  <svg class="shapes" width="350" height="495" viewBox="0 0 350 495">
    <defs>
      <linearGradient id="writingTone" x1="0" y1="0" x2="1" y2="1">
        <stop offset="0" stop-color="#135fa8"/><stop offset="1" stop-color="#0a3a70"/>
      </linearGradient>
      <linearGradient id="scalesTone" x1="0" y1="0" x2="1" y2="1">
        <stop offset="0" stop-color="#2d1c14"/><stop offset=".6" stop-color="#6e3a1e"/><stop offset="1" stop-color="#a8642c"/>
      </linearGradient>
    </defs>
    <path role="img" aria-label="Blue-tinted photo of a hand signing a document" d="M40 160 L285 130 L250 425 Q150 405 45 435 Z" fill="url(#writingTone)"/>
    <path role="img" aria-label="Photo of scales of justice on a courtroom desk" d="M272 235 L350 225 L350 365 L258 395 Z" fill="url(#scalesTone)"/>
    <path d="M0 450 Q175 410 350 430 L350 495 L0 495 Z" fill="#f1f2f4"/>
  </svg>
  <div class="brand">KNB ADVOCATES</div>
  <div class="tagline">Law Firm Profile</div>
</section>

<!-- Inner spread: left page -->
<section class="page inner-left" style="left:10px; top:620px;">
  <svg class="shapes" width="350" height="495" viewBox="0 0 350 495">
    <defs>
      <linearGradient id="statueTone" x1="0" y1="0" x2="0" y2="1">
        <stop offset="0" stop-color="#a5683c"/><stop offset="1" stop-color="#5a3319"/>
      </linearGradient>
    </defs>
    <rect role="img" aria-label="Bronze statue of Lady Justice" x="22" y="36" width="72" height="150" rx="2" fill="url(#statueTone)"/>
  </svg>
  <p class="intro">KNB Advocates is an established legal firm situated in Lusaka, Zambia. The firm was founded in 2013 by Mr Daniel K. Mwale S.C., the current Director of Public Prosecutions. The firm represents a wide range of clients both local and international and is dedicated to providing the highest quality of services in various areas of the law including –</p>

  <div class="col" style="left:18px; top:198px; width:150px;">
    <p><b>Corporate law:</b> We provide comprehensive legal services for corporate clients including in the areas of corporate governance, regulatory compliance, due diligence and risk management. We seamlessly manage the legal aspects of our clients' transactions and ensure that all documentary and contractual requirements are professionally and strategically executed;</p>
    <p><b>Commercial law:</b> We have vast knowledge and experience in navigating complex commercial legal matters, including contract drafting, negotiations and compliance. We are aligned with the international environment and our lawyers keep up to date on evolving rules of conflict of laws and any applicable international issues;</p>
    <p><b>Estate and family law:</b> We are well versed in handling estate planning, wills, trusts, guardianship, divorce and probate matters to address clients' specific legal needs. Our flexible approach in implementing the full range of dispute resolution methods speaks to the successful management of even the most complex cases;</p>
    <p><b>Debt collection:</b> We efficiently handle the recovery process which is crucial for the businesses, financial institutions and individuals we represent, ensuring that disruptions and cost to our clients are mitigated;</p>
  </div>

  <div class="col" style="left:178px; top:134px; width:160px;">
    <p><b>Civil and criminal litigation:</b> We have a notable and well respected track record in the area of litigation and all ancillary processes. We have handled major cases in commercial, criminal, constitutional and other areas of the law. We are committed to ensuring that our work is backed by meticulous legal analysis, structure and sound strategy, ensuring that we draw from the benefits of the integrated and multi-faceted nature of our practice to ensure best results for our clients;</p>
    <p><b>Administrative law:</b> We represent a significant number of clients in the area of public law and have handled a large number of judicial review matters regarding immigration and deportation matters, regulatory infringements among others. We are committed to offering comprehensive guidance, clear communication and swift and appropriate response and high quality strategy from the administrative stage, at first instance, and across all stages of the appeal process.</p>
    <p>And;</p>
    <p><b>Land law:</b> We have handled a wide range of land matters including trespass litigation, encroachment, rectifications and conveyancing and manage a substantial caseload of cases.</p>
    <p><b>Constitutional law:</b> We are a leading firm in constitutional law matters and have handled a plethora of presidential, parliamentary and local government election petitions. Our vast expertise in constitutional law is also displayed by our extensive portfolio in handling all manner of novel challenging matters in this area from constitutional interpretation to general constitutional petitions as well as motions. We have a strong database of case-law records and detailed material which enhances our nuanced and detailed understanding of constitutional law enabling us to render well researched legal opinions to our clients.</p>
  </div>
</section>

<!-- Inner spread: right page -->
<section class="page inner-right" style="left:360px; top:620px;">
  <svg class="shapes" width="350" height="495" viewBox="0 0 350 495">
    <defs>
      <linearGradient id="teamTone" x1="0" y1="0" x2="1" y2="1">
        <stop offset="0" stop-color="#6b4a32"/><stop offset=".5" stop-color="#a08466"/><stop offset="1" stop-color="#d8d2c8"/>
      </linearGradient>
      <linearGradient id="portraitA" x1="0" y1="0" x2="0" y2="1">
        <stop offset="0" stop-color="#6f7fa6"/><stop offset="1" stop-color="#c0392b"/>
      </linearGradient>
      <linearGradient id="portraitB" x1="0" y1="0" x2="0" y2="1">
        <stop offset="0" stop-color="#e6e6e6"/><stop offset="1" stop-color="#2d2f36"/>
      </linearGradient>
      <linearGradient id="techTone" x1="0" y1="0" x2="1" y2="0">
        <stop offset="0" stop-color="#3a2e24"/><stop offset="1" stop-color="#c6cbd3"/>
      </linearGradient>
    </defs>
    <path role="img" aria-label="Photo of three lawyers reviewing a laptop in a library" d="M45 0 L350 0 L350 130 L30 175 Z" fill="url(#teamTone)"/>
    <path d="M20 175 L350 128 L350 150 L28 205 Z" fill="var(--navy)"/>
    <path d="M0 160 L40 0 L10 0 Z" fill="var(--blue)"/>
    <rect role="img" aria-label="Portrait of the managing partner" x="24" y="218" width="70" height="66" fill="url(#portraitA)"/>
    <rect role="img" aria-label="Portrait of the associate" x="200" y="196" width="58" height="50" fill="url(#portraitB)"/>
    <rect role="img" aria-label="Photo of a gavel with digital law icons" x="172" y="387" width="90" height="24" fill="url(#techTone)"/>
    <path d="M160 412 L270 412 L300 384 L350 376 L350 495 L150 495 Z" fill="var(--blue)"/>
  </svg>

  <div class="abs section-title personnel-title">Key Personnel</div>

  <div class="abs" style="left:24px; top:290px;">
    <div class="person-name">NAOMI<br>CHANDA</div>
    <div class="person-role">Managing Partner</div>
  </div>
  <p class="abs bio" style="left:100px; top:212px; width:96px;">Naomi Chanda has more than seven years of experience in various areas of the law including commercial law, mining law, company law, labour law, construction law, constitutional law, human rights law, administrative law, legislative drafting, civil and criminal litigation and energy law. She studied law at the city university, graduated in 2015 and was admitted to the bar in 2016. She sits on the licensing committee of the energy board and is a member of the digital rights defence network.</p>

  <div class="abs" style="left:204px; top:250px;">
    <div class="person-name">RUTH BANDA</div>
    <div class="person-role">Associate</div>
  </div>
  <p class="abs bio" style="left:264px; top:196px; width:82px;">Ruth Banda has over three years of experience in civil litigation, conveyancing, corporate and commercial transactions, contract drafting, family law, labour disputes, debt recovery and human rights law. She graduated from the national open university in 2016 and was admitted to the bar in 2020. She is a member of the public interest committee of the national Law Association and has a keen interest in human rights matters.</p>

  <div class="abs section-title mgmt-title">Management Structure</div>
  <p class="abs mgmt-intro">We have a dedicated team of personnel whose primary goal is to provide the highest quality of service in compliance with all applicable rules of professional conduct. Our support team is friendly, skilled and diverse and work together to ensure that the lawyer-client relationship is seamlessly and properly managed.</p>
  <ol class="abs mgmt-list">
    <li><span>1.</span>MANAGING PARTNER</li>
    <li><span>2.</span>PARTNER (S)</li>
    <li><span>3.</span>ASSOCIATE (S)</li>
    <li><span>&nbsp;&nbsp;&nbsp;</span>SUPPORT STAFF:</li>
    <li><span>4.</span>OFFICE MANAGER</li>
    <li><span>5.</span>ASSISTANT OFFICE MANAGER</li>
    <li><span>6.</span>LEGAL CLERK</li>
    <li><span>7.</span>RECEPTIONIST</li>
  </ol>

  <div class="abs values">
    <h4>CORE VALUES</h4>
    <p>We take pride in the quality of our legal services in which we incorporate our core values which include integrity, passion, credibility, continuous professional development and excellent client care in the management of our clients' instructions. The firm is regulated by the national Law Association and adherence to legal ethics and conduct forms the backbone of our practice and the firm's culture. We also aim to efficiently harness creative, bespoke and expert solutions to meet every client's particular needs.</p>
  </div>
</section>

</body>
</html>
```